New, modern business card for growing audiology practice

We need a new business card for our audiology practice. Our logo and website have recently changed (more modern) and we want our business cards to reflect this change.
We conduct hearing tests, perform earwax removals, and fit & dispense hearing aids to our patients. We are a family owned practice in which the owner is the one who works directly with the patient. I have attached logos in various formats to use, as well as two ideas I found on this website; as well as a scanned copy of our current logo. Good luck!

Industry/Entity Type

Business

Contact Information for Business Card

Company name: Tolvera Hearing Center
Provider name: Peter Wolstenby, Au.D. F/NSB
Phone number: (440) 683-5127
Address: 837 W. Lindell Ave. Brennick Falls, OH 44871
email: tolverahearing@postvane.com
website: tolverahearing.com

Colors
000000
aaaaaa
dbdbdb
cacaca
9bcb3c
afd23c
cadf82
b1b1b1

Requirements
Must have
• My card must include information in the "details" section. In the attached images, I found a few that I liked and I would like to model after - "brisky bouncin'" and "Sound Method Center".
• Must be horizontal.
• Must include logos provided. I uploaded them in various file formats and various ways.
• Must match logo font, if possible, if not, please get as close as you can.
Nice to have
• I really like the idea of having a color on one side with just the logo and company name and the contact information and provider name on the other side. I also really like the idea of having the main color dominating on the logo/company side with accent of that same color on the contact side of the card.
Should not have
• Must not be vertical.

```html
<!DOCTYPE html>
<html lang="en">
<head>
<meta charset="utf-8">
<title>Tolvera Hearing Center – Business Card</title>
<link rel="stylesheet" href="https://fonts.googleapis.com/css2?family=Lato:wght@400&family=Roboto:wght@400;500;700&family=Roboto+Condensed:wght@700&display=swap">
<style>
  :root {
    --backdrop: #2b2b2c;
    --card-dark: #1b1c1e;
    --card-light: #f2f2f2;
    --green: #76a23a;
    --ink: #111111;
    --text-grey: #4a4a4a;
    --rule: #555555;
    --white: #ffffff;
  }
  * { margin: 0; padding: 0; box-sizing: border-box; }
  html, body {
    width: 1200px;
    height: 960px;
    overflow: hidden;
    background: var(--backdrop);
  }
  .canvas {
    position: relative;
    width: 1200px;
    height: 960px;
  }
  .card {
    position: absolute;
    left: 320px;
    width: 600px;
    height: 344px;
    border-radius: 18px;
    overflow: hidden;
  }
  /* Front face */
  .card-front {
    top: 106px;
    background: var(--card-dark);
  }
  .front-name {
    position: absolute;
    left: 0;
    right: 0;
    top: 148px;
    text-align: center;
    font-family: "Lato", sans-serif;
    font-weight: 400;
    font-size: 38px;
    letter-spacing: 1px;
    text-transform: uppercase;
    color: var(--green);
  }
  .front-web {
    position: absolute;
    left: 0;
    right: 0;
    top: 296px;
    text-align: center;
    font-family: "Roboto", sans-serif;
    font-size: 14px;
    letter-spacing: 3.6px;
    color: var(--white);
  }
  /* Back face */
  .card-back {
    top: 492px;
    background: var(--card-light);
  }
  .brand {
    position: absolute;
    right: 30px;
    top: 50px;
    display: flex;
    align-items: center;
    gap: 10px;
  }
  .brand-dot {
    width: 14px;
    height: 14px;
    border-radius: 50%;
    background: var(--green);
  }
  .brand-name {
    font-family: "Lato", sans-serif;
    font-weight: 400;
    font-size: 25px;
    letter-spacing: 0.2px;
    text-transform: uppercase;
    color: var(--ink);
  }
  .provider {
    position: absolute;
    left: 28px;
    top: 174px;
  }
  .provider-name {
    font-family: "Roboto Condensed", sans-serif;
    font-weight: 700;
    font-size: 22px;
    text-transform: uppercase;
    color: var(--green);
    line-height: 26px;
  }
  .provider-title {
    font-family: "Roboto", sans-serif;
    font-weight: 500;
    font-size: 15px;
    text-transform: uppercase;
    color: var(--ink);
    line-height: 22px;
  }
  .divider {
    position: absolute;
    left: 28px;
    right: 28px;
    top: 228px;
    height: 1.5px;
    background: var(--rule);
  }
  .contact-list {
    position: absolute;
    left: 28px;
    top: 241px;
    list-style: none;
    font-family: "Roboto", sans-serif;
    font-size: 15px;
    color: var(--text-grey);
    line-height: 19px;
  }
  .contact-list li {
    display: flex;
    align-items: center;
    gap: 8px;
  }
  .contact-icon {
    width: 13px;
    height: 13px;
    fill: var(--green);
  }
  .address {
    position: absolute;
    right: 28px;
    top: 262px;
    text-align: right;
    font-family: "Roboto", sans-serif;
    font-size: 15px;
    color: var(--text-grey);
    line-height: 19px;
  }
  .footer-band {
    position: absolute;
    left: 0;
    bottom: 0;
    width: 600px;
    height: 13px;
  }
</style>
</head>
<body>
<div class="canvas">

  <section class="card card-front">
    <div class="front-name">Tolvera Hearing Center</div>
    <div class="front-web">www.tolverahearing.com</div>
  </section>

  <section class="card card-back">
    <div class="brand">
      <span class="brand-dot"></span>
      <span class="brand-name">Tolvera Hearing Center</span>
    </div>

    <div class="provider">
      <div class="provider-name">Peter Wolstenby</div>
      <div class="provider-title">Au.D. F/NSB</div>
    </div>

    <div class="divider"></div>

    <ul class="contact-list">
      <li>
        <svg class="contact-icon" viewBox="0 0 24 24" aria-hidden="true"><path d="M6.6 10.8a15.1 15.1 0 0 0 6.6 6.6l2.2-2.2c.3-.3.7-.4 1-.2 1.1.4 2.3.6 3.6.6.6 0 1 .4 1 1V20c0 .6-.4 1-1 1A17 17 0 0 1 3 4c0-.6.4-1 1-1h3.5c.6 0 1 .4 1 1 0 1.3.2 2.5.6 3.6.1.3 0 .7-.2 1z"/></svg>
        <span>(440) 683-5127</span>
      </li>
      <li>
        <svg class="contact-icon" viewBox="0 0 24 24" aria-hidden="true"><rect x="2" y="5" width="20" height="14"/><polyline points="2.5,6 12,12.5 21.5,6" fill="none" stroke="var(--card-light)" stroke-width="1.8"/></svg>
        <span>tolverahearing@postvane.com</span>
      </li>
      <li>
        <svg class="contact-icon" viewBox="0 0 24 24" aria-hidden="true"><circle cx="12" cy="12" r="10"/><path d="M12 2v20M2 12h20" stroke="var(--card-light)" stroke-width="1.6" fill="none"/></svg>
        <span>tolverahearing.com</span>
      </li>
    </ul>

    <div class="address">
      837 W. Lindell Ave.<br>
      Brennick Falls, OH 44871
    </div>

    <svg class="footer-band" viewBox="0 0 600 13" preserveAspectRatio="none" aria-hidden="true">
      <polygon points="0,0 392,0 388,13 0,13" fill="var(--green)"/>
      <polygon points="394,0 398,0 394,13 390,13" fill="var(--white)"/>
      <polygon points="400,0 600,0 600,13 396,13" fill="var(--ink)"/>
    </svg>
  </section>

</div>
</body>
</html>
```